Stonebridge Building and Projects business cards

A business card with watermark background (construction work)

Company logo attached

Home improvement projects
House renovations
Bathroom and kitchen renovations
House extensions
New builds and granny flats

Director Omar Haddani
(Phone number)
omar@sbpbuilding.com.au
(Instagram logo) sbp_building

```html
<!DOCTYPE html>
<html lang="en">
<head>
<meta charset="UTF-8">
<title>Stonebridge Building and Projects – Business Cards</title>
<link href="https://fonts.googleapis.com/css2?family=Roboto:wght@400;500;700&display=swap" rel="stylesheet">
<style>
  :root {
    --brand-blue: #1f7bc1;
    --brand-blue-dark: #165f98;
    --charcoal: #3a3d42;
    --text-dark: #2b2e33;
    --card-white: #f7f8f9;
    --page-bg: #e6e8eb;
    --watermark: #ebedef;
  }
  * { margin: 0; padding: 0; box-sizing: border-box; }
  html, body {
    width: 1200px; height: 1050px; overflow: hidden;
    background: var(--page-bg);
    font-family: "Roboto", Arial, sans-serif;
  }
  .sheet {
    position: relative; width: 1200px; height: 1050px;
    display: flex; flex-direction: column; align-items: center;
    justify-content: center; gap: 60px;
  }
  .card {
    position: relative; width: 640px; height: 370px;
    background: var(--card-white); border-radius: 22px; overflow: hidden;
    box-shadow: 0 8px 24px rgba(0,0,0,0.15);
  }

  /* Brand lockup */
  .brand { display: flex; flex-direction: column; align-items: flex-start; }
  .brand-name {
    display: flex; align-items: center; gap: 10px;
    color: var(--brand-blue); font-weight: 700; font-size: 26px; line-height: 1.1;
  }
  .brand-mark { width: 16px; height: 16px; background: var(--brand-blue); flex: none; }
  .brand-rule { width: 100%; height: 2px; background: var(--brand-blue); margin: 8px 0 6px; }
  .brand-tagline {
    color: var(--brand-blue); font-weight: 500; font-size: 18px;
    border-bottom: 2px solid var(--brand-blue); padding-bottom: 2px;
  }

  /* Front */
  .front .watermark {
    position: absolute; left: 0; top: 0; width: 100%; height: 230px;
    background: radial-gradient(ellipse at 40% 60%, var(--watermark), var(--card-white) 70%);
  }
  .front .brand { position: absolute; left: 150px; top: 70px; }
  .services-band {
    position: absolute; left: 0; top: 232px; width: 100%; height: 72px;
    background: var(--brand-blue); color: #fff;
    display: flex; flex-direction: column; justify-content: center; align-items: center;
    font-size: 15.5px; line-height: 1.55;
  }
  .services-band .sep { margin: 0 8px; }
  .front-contacts {
    position: absolute; left: 0; top: 304px; width: 100%; height: 66px;
    display: flex; justify-content: center; align-items: center; gap: 34px;
    color: var(--text-dark); font-size: 15px;
  }
  .contact-item { display: flex; align-items: center; gap: 8px; }
  .icon-dot {
    width: 18px; height: 18px; border-radius: 50%; background: var(--brand-blue);
    display: inline-flex; align-items: center; justify-content: center;
  }

  /* Back */
  .back .brand { position: absolute; left: 36px; top: 118px; }
  .back .brand-name { font-size: 24px; }
  .back .wave { position: absolute; left: 0; top: 0; }
  .person { position: absolute; right: 40px; top: 30px; text-align: right; }
  .person-name { color: var(--brand-blue); font-weight: 700; font-size: 22px; }
  .person-role { color: var(--text-dark); font-size: 14px; margin-top: 3px; }
  .back-contacts {
    position: absolute; right: 36px; top: 178px; list-style: none;
    color: #fff; font-size: 16px; line-height: 28px; text-align: right;
  }
  .back-contacts li { display: flex; justify-content: flex-end; align-items: center; gap: 12px; }
  .back-contacts svg { flex: none; }
</style>
</head>
<body>
<main class="sheet">

  <section class="card front">
    <div class="watermark" role="img" aria-label="Faint background image of construction work"></div>
    <div class="brand">
      <div class="brand-name"><span class="brand-mark"></span>Stonebridge Building and Projects</div>
      <div class="brand-rule"></div>
      <div class="brand-tagline">Solid from the ground up!</div>
    </div>
    <div class="services-band">
      <div>Home Improvement Projects<span class="sep">|</span>House Renovations<span class="sep">|</span>House Extensions</div>
      <div>Bathroom &amp; Kitchen Renovations<span class="sep">|</span>New Builds &amp; Granny Flats</div>
    </div>
    <div class="front-contacts">
      <span class="contact-item"><span class="icon-dot"></span>sbp_building</span>
      <span class="contact-item">
        <svg width="18" height="18" viewBox="0 0 18 18" aria-hidden="true">
          <circle cx="9" cy="9" r="8" fill="var(--brand-blue)"/>
          <ellipse cx="9" cy="9" rx="3.5" ry="7" fill="none" stroke="#fff" stroke-width="1.2"/>
          <line x1="2" y1="9" x2="16" y2="9" stroke="#fff" stroke-width="1.2"/>
        </svg>sbpbuilding.com.au</span>
    </div>
  </section>

  <section class="card back">
    <svg class="wave" width="640" height="370" viewBox="0 0 640 370" aria-hidden="true">
      <defs>
        <path id="swoosh" d="M640 86 C510 92 390 108 335 162 C285 216 262 345 80 372 L700 400 L700 86 Z"/>
      </defs>
      <use href="#swoosh" fill="var(--charcoal)"/>
      <use href="#swoosh" fill="var(--card-white)" transform="translate(14 10)"/>
      <use href="#swoosh" fill="var(--brand-blue)" transform="translate(20 16)"/>
      <path d="M0 345 C60 350 110 358 160 370 L0 370 Z" fill="var(--brand-blue)"/>
    </svg>
    <div class="brand">
      <div class="brand-name"><span class="brand-mark"></span>Stonebridge Building<br>and Projects</div>
      <div class="brand-rule"></div>
      <div class="brand-tagline">Solid from the ground up!</div>
    </div>
    <div class="person">
      <div class="person-name">Omar Haddani</div>
      <div class="person-role">Managing Director</div>
    </div>
    <ul class="back-contacts">
      <li>0412 380 517
        <svg width="16" height="16" viewBox="0 0 16 16" aria-hidden="true"><path d="M4 2 L6.5 2 L7.5 5 L6 6.5 C7 8.5 8 9.5 9.5 10 L11 8.5 L14 9.5 L14 12 C14 13 13 14 12 14 C7 14 2 9 2 4 C2 3 3 2 4 2 Z" fill="#fff"/></svg></li>
      <li>sbp_building
        <svg width="16" height="16" viewBox="0 0 16 16" aria-hidden="true"><circle cx="8" cy="8" r="7" fill="#fff"/></svg></li>
      <li>omar@sbpbuilding.com.au
        <svg width="16" height="16" viewBox="0 0 16 16" aria-hidden="true"><rect x="1.5" y="3.5" width="13" height="9" fill="none" stroke="#fff" stroke-width="1.5"/><path d="M1.5 3.5 L8 9 L14.5 3.5" fill="none" stroke="#fff" stroke-width="1.5"/></svg></li>
      <li>www.sbpbuilding.com.au
        <svg width="16" height="16" viewBox="0 0 16 16" aria-hidden="true"><circle cx="8" cy="8" r="6.5" fill="none" stroke="#fff" stroke-width="1.4"/><ellipse cx="8" cy="8" rx="3" ry="6.5" fill="none" stroke="#fff" stroke-width="1.2"/><line x1="1.5" y1="8" x2="14.5" y2="8" stroke="#fff" stroke-width="1.2"/></svg></li>
    </ul>
  </section>

</main>
</body>
</html>
```